Leadership training for women Business + Spirit

I need a flyer for a leadership training to hand out after I've been doing public speaking. I would also like to send it as a PDF. so maybe A4 is a good size. I will probably also need a brochure, with some more in depth information, but to start with I like to just give them something so they get inspired to contact me for more information. You can see more of my style on www.brightmeadow.se . Its a training that combines business with spirit, heart with intellect. We focus both on strict leadership skills such as Setting objectives aligned with strategy, assess performance and spiritual practices such as meditation, connecting with your unique essence. I like the deign to communicate business and professional together with warmth, life and joy. Colourful with style. Empowerment. The attached style guide does not have to be followed strictly but please use it in combination with my site www.brightmeadow.se I've the logo in many different sizes. I've added the smallest one below. Use any images that you think might fit, doesn't have to be from my website, it could be from your resources. I've added some other images here in the brief too, I have many more but can't attach all of it :-).
Target Market(s)
Women in leadership positions age 30 - 60
Industry/Entity Type
Leadership
Look and feel

```html
<!DOCTYPE html>
<html lang="sv">
<head>
<meta charset="utf-8">
<title>Bright Meadow Ledarskap – flyer</title>
<link href="https://fonts.googleapis.com/css2?family=Oswald:wght@500;600&family=Lato:wght@400;700&display=swap" rel="stylesheet">
<style>
  :root{
    --navy:#243a5c;
    --navy-deep:#1c2f4c;
    --orange:#f07f0c;
    --ink:#1c1c1c;
    --white:#ffffff;
    --page-bg:#ececec;
    --heather:#a8308f;
    --heather-light:#e7a6d6;
  }
  *{box-sizing:border-box;margin:0;padding:0}
  html,body{width:1200px;height:1200px;overflow:hidden;background:var(--page-bg)}
  .flyer{position:absolute;left:190px;top:25px;width:820px;height:1150px;background:var(--white);overflow:hidden;font-family:'Lato',sans-serif;box-shadow:0 2px 10px rgba(0,0,0,.15)}
  .hero-bg{position:absolute;left:0;top:0;width:820px;height:470px}
  .abs{position:absolute}
  .headline{left:38px;top:30px;width:770px;font-family:'Oswald',sans-serif;font-weight:600;font-size:25.5px;line-height:30px;color:var(--white);text-transform:uppercase;letter-spacing:-.2px}
  .rule{height:4px;background:var(--orange)}
  .intro{left:42px;top:115px;width:740px;color:var(--white);font-size:12.3px;line-height:16px}
  .points{left:40px;top:208px;width:720px;list-style:none;color:var(--white);font-size:14px;line-height:18px}
  .points li{position:relative;padding-left:13px;margin-bottom:14.5px}
  .points li::before{content:"";position:absolute;left:1px;top:5px;width:6px;height:6px;border-top:2.5px solid var(--orange);border-right:2.5px solid var(--orange);transform:rotate(45deg)}
  .portrait{left:566px;top:377px;width:224px;height:224px;border-radius:50%;border:6px solid var(--navy);overflow:hidden}
  .portrait-shadow{left:590px;top:610px;width:180px;height:10px;border-radius:50%;background:radial-gradient(ellipse,rgba(0,0,0,.3),rgba(0,0,0,0) 70%)}
  .leader-title{left:41px;top:480px;font-family:'Oswald',sans-serif;font-weight:500;font-size:19px;color:var(--orange)}
  .leader-bio{left:41px;top:521px;width:500px;font-size:14px;line-height:17.7px;color:var(--ink)}
  .mission{left:40px;top:656px;width:755px;font-size:12.4px;line-height:16.2px;color:var(--ink)}
  .guarantee{left:0;top:720px;width:820px;height:38px;background:var(--orange);color:var(--white);font-family:'Oswald',sans-serif;font-weight:600;font-size:23px;line-height:38px;text-align:center;letter-spacing:-.3px}
  .promise{left:40px;top:769px;font-size:18.5px;font-weight:700;color:var(--navy)}
  .extras-lead{left:43px;top:826px;font-size:14px;color:var(--ink)}
  .extras{top:850px;list-style:none;font-size:14px;line-height:24.5px;color:var(--ink)}
  .extras li{position:relative;padding-left:14px}
  .extras li::before{content:"";position:absolute;left:1px;top:10px;width:5px;height:5px;border-radius:50%;background:var(--ink)}
  .heather{left:0;top:880px;width:820px;height:234px;background:
    linear-gradient(180deg,var(--white) 0%,rgba(255,255,255,0) 28%),
    radial-gradient(ellipse at 30% 60%,var(--heather-light),rgba(231,166,214,0) 55%),
    linear-gradient(180deg,#d9a7c9 20%,var(--heather) 70%,#6d1f63 100%)}
  .footer{left:0;top:1114px;width:820px;height:36px;background:var(--navy-deep);display:flex;align-items:center;justify-content:center;gap:14px;color:var(--white);font-size:17px;letter-spacing:.3px}
  .footer .dot{width:11px;height:11px;border-radius:50%;background:var(--orange)}
</style>
</head>
<body>
<div class="flyer">
  <svg class="hero-bg" viewBox="0 0 820 470" role="img" aria-label="Fotografi av mörkblått hav bakom rubriken">
    <defs>
      <linearGradient id="sea" x1="0" y1="0" x2="0" y2="1">
        <stop offset="0" stop-color="#2a4366"/>
        <stop offset="1" stop-color="#1f3455"/>
      </linearGradient>
    </defs>
    <path d="M0 0H820V380C700 330 640 350 520 410C420 460 300 470 180 440C100 420 40 390 0 372Z" fill="url(#sea)"/>
    <path d="M0 372C40 390 100 420 180 440C300 470 420 460 520 410C640 350 700 330 820 380" fill="none" stroke="#ffffff" stroke-width="10"/>
    <path d="M0 385C40 405 100 435 180 452C300 480 420 468 520 418C640 360 700 345 820 398" fill="none" stroke="var(--orange)" stroke-width="6"/>
  </svg>

  <h1 class="abs headline">Är du en kvinna som gillar att prestera, vill förbättra ditt ledarskap och leva ett själfullt liv?</h1>
  <div class="abs rule" style="left:38px;top:93px;width:492px"></div>

  <p class="abs intro">Utbildningen varvar det personliga med det professionella så att du samtidigt som du ökar din arbetsprestation även fördjupar kontakten med ditt inre, får nya perspektiv, hanterar stressen konstruktivt och skapar ett liv med god balans - både på arbetet och livet som helhet.<br>Utbildningen består av 2 fristående moduler på 2 + 3 dagar + online uppföljning. Man kan alltså välja att göra 2 eller 5 dagar, allteftter behov. Modulerna är uppbyggda så att innehållet passar oavsett om du leder projekt, medarbetare eller större enheter:</p>

  <ul class="abs points">
    <li>Vi arbetar med att effektivisera arbetstiden genom analys, prioriteringar, mål och time management.</li>
    <li>Vi arbetar med kommunikation genom coaching, feedback, svåra samtal och stakeholder management.</li>
    <li>Vi arbetar med stresshantering genom avslappning, mindfulness, mental träning och tankens kraft.</li>
    <li>Vi arbetar med inre kontakt och den feminina essensen genom meditationer, samtal och övningar för ökad med&nbsp; vetenhet och djupare förankring i själ och hjärta.</li>
  </ul>

  <div class="abs portrait-shadow"></div>
  <svg class="abs portrait" viewBox="0 0 212 212" role="img" aria-label="Porträttfoto av kursledaren">
    <rect width="212" height="212" fill="#8a7d74"/>
    <rect y="120" width="212" height="92" fill="#2b3245"/>
  </svg>

  <h2 class="abs leader-title">Kursledaren Karin Lindqvist Berg :</h2>
  <p class="abs leader-bio">Jag är en modern mystiker och ledarskapsutvecklare som de senaste 16 åren har tillhandahållit tusentals timmar med coaching, kurser och föreläsningar. Antingen har det varit ledarskapsutbildningar med fokus på prestation och leverans på t.ex. Nordbank, Mejerigården, Kronbryggeriet, Stegverk, Tryggvik, Vindkraft Nord, Snabbköp m.fl. eller utbildningar med fokus på meditation och den feminina essensen. Nu är det dags att kombinera dessa områden!</p>

  <p class="abs mission">Med Bright Meadow Ledarskap vill jag ge ett rum till just kvinnor i ledande positioner att ta sig an det arbete och de enorma möjligheter som ligger framför oss om vi fokuserar på vårt ledarskap, omvandlar stressen till kraft, låter det djupa varandet guida oss och öppnar vårt sinne för den kreativitet och struktur som behövs för att möta morgondagens utmaningar.</p>

  <div class="abs guarantee">PENGAR-TILLBAKA-GARANTI : Om du inte är nöjd så får du 100 % tillbaka !</div>

  <p class="abs promise">Du kommer att lämna utbildningen påfylld, inspirerad och förberedd!</p>
  <div class="abs rule" style="left:40px;top:797px;width:570px;height:3px"></div>

  <p class="abs extras-lead">Dessutom får du med dig :</p>
  <ul class="abs extras" style="left:43px">
    <li>Personlig handlings -och utvecklingsplan</li>
    <li>Konkreta verktyg för ditt välmående</li>
  </ul>
  <ul class="abs extras" style="left:360px">
    <li>Konkreta verktyg för ledarskapet</li>
    <li>Nätverk av likasinnade kvinnor</li>
  </ul>

  <div class="abs heather" role="img" aria-label="Fotografi av blommande ljung i rosa och lila toner"></div>

  <div class="abs footer"><span class="dot"></span><span>www.brightmeadow.se</span></div>
</div>
</body>
</html>
```